NZ First of it's kind solutions directory and marketplace for busy Mums needs a business card design

We need a business card design for our new nationwide business in NZ (long term plans to go global). We provide solutions to the everyday challenges that busy Mums face by connecting them with quality communities and suppliers of carefully selected, relevant products and services. We sell direct via our online marketplace. The final design should communicate our values of inclusivity, quality and smart solutions. Colours should incorporate our logo colour palette of #477077 and #6ba8b2. Our website is at https://www.brightnestmums.example

Target Market(s)

busy Mums, Age 28 – 50, female, income over $100K, location main centres NZ primarily but NZ wide. Is likely juggling work or career with a young family. Probably had hobbies which have fallen by the wayside.
-Wants to succeed in her chosen career without compromising on family life
-to successfully juggle her career without feeling like she is compromising her children
- Is time poor, something always has to give and it’s generally her health (she’ll stay up late, get stressed)
- probably ex corporate or professional career. Has discretional income

Industry/Entity Type

Business

Contact Information for Business Card

Lena Forbisher, Founder, BrightNestMums.example (Strapline Tap; Gather; Sorted), 47 Kowhai Terrace, Ellerslie, Auckland 1051, New Zealand. Mob: 021 483 517 Ph: +64 (0)9 571 4860

Font styles to use
Other font styles liked:
• Raleway, and/or Architects Daughter

Colors
00a990
33b8a4
86cfc6
cfeae6

Requirements
Must have
• the above details, streamline. the logo and colours associated with those logos
Should not have
• foil or metallic colours

```html
<!DOCTYPE html>
<html lang="en">
<head>
<meta charset="utf-8">
<title>BrightNest Mums – Business Card</title>
<link rel="stylesheet" href="https://fonts.googleapis.com/css2?family=Roboto:wght@400;500;700&family=Roboto+Condensed:ital,wght@0,400;0,600;1,400&display=swap">
<style>
  :root {
    --teal-deep: #477077;
    --teal-card: #3f5e67;
    --teal-light: #6ba8b2;
    --ink: #3a3a3a;
    --paper: #f5f5f5;
    --backdrop: #e4e4e4;
  }
  * { margin: 0; padding: 0; box-sizing: border-box; }
  html, body { width: 1200px; height: 576px; overflow: hidden; }
  body {
    position: relative;
    background: var(--backdrop);
    font-family: "Roboto Condensed", "Arial Narrow", sans-serif;
    color: var(--ink);
  }
  .card {
    position: absolute;
    top: 138px;
    border-radius: 13px;
    overflow: hidden;
  }
  /* Front */
  .card-front {
    left: 82px; width: 485px; height: 293px;
    background: var(--teal-card);
    color: #fff;
    text-align: center;
  }
  .front-wordmark {
    position: absolute; left: 0; right: 0; top: 112px;
    font-family: "Roboto", sans-serif;
    font-weight: 700;
    font-size: 42px;
    letter-spacing: -0.5px;
    line-height: 1;
  }
  .front-strapline {
    position: absolute; left: 0; right: 0; top: 248px;
    top: 170px;
    font-family: "Roboto", sans-serif;
    font-size: 13px;
    letter-spacing: 4.5px;
    line-height: 1;
  }
  /* Back */
  .card-back {
    left: 602px; width: 480px; height: 291px;
    background: var(--paper);
  }
  .brand-block {
    position: absolute; left: 36px; top: 76px; width: 196px;
    text-align: center;
  }
  .brand-dot {
    display: block; margin: 0 auto 16px;
    width: 40px; height: 40px; border-radius: 50%;
    background: var(--teal-deep);
  }
  .brand-wordmark {
    font-family: "Roboto", sans-serif;
    font-weight: 700;
    font-size: 23px;
    letter-spacing: -0.4px;
    color: var(--teal-deep);
    line-height: 1;
  }
  .brand-strapline {
    margin-top: 8px;
    font-family: "Roboto", sans-serif;
    font-size: 8.5px;
    letter-spacing: 2.6px;
    color: var(--ink);
  }
  .brand-strapline .sep, .front-strapline .sep { color: var(--teal-light); }
  .front-strapline .sep { color: #fff; }
  .contact {
    position: absolute; left: 264px; top: 56px;
  }
  .contact-name {
    font-weight: 600; font-size: 20px; color: var(--teal-card); line-height: 1.1;
  }
  .contact-role { font-style: italic; font-size: 12.5px; margin-top: 3px; }
  .contact-address { margin-top: 18px; font-size: 13px; line-height: 18px; }
  .contact-lines { list-style: none; margin-top: 9px; font-size: 13px; }
  .contact-lines li { display: flex; align-items: center; height: 18.5px; }
  .contact-lines svg { width: 10px; height: 10px; margin: 0 9px 0 4px; fill: var(--teal-light); }
</style>
</head>
<body>
  <section class="card card-front" aria-label="Card front">
    <div class="front-wordmark">BrightNest Mums</div>
    <div class="front-strapline">TAP <span class="sep">|</span> GATHER <span class="sep">|</span> SORTED</div>
  </section>

  <section class="card card-back" aria-label="Card back">
    <div class="brand-block">
      <span class="brand-dot"></span>
      <div class="brand-wordmark">BrightNestMums</div>
      <div class="brand-strapline">TAP <span class="sep">|</span> GATHER <span class="sep">|</span> SORTED</div>
    </div>

    <div class="contact">
      <div class="contact-name">Lena Forbisher</div>
      <div class="contact-role">Founder</div>
      <address class="contact-address" style="font-style:normal">
        47 Kowhai Terrace, Ellerslie,<br>Auckland 1051, New Zealand
      </address>
      <ul class="contact-lines">
        <li><svg viewBox="0 0 10 10"><rect x="2" y="0" width="6" height="10" rx="1.2"/></svg>021 483 517</li>
        <li><svg viewBox="0 0 10 10"><path d="M0 3 Q5 0 10 3 L9 5 L7 4 L7 3 Q5 2 3 3 L3 4 L1 5 Z M2 6 H8 V10 H2 Z"/></svg>+64 (0)9 571 4860</li>
        <li><svg viewBox="0 0 10 10"><path d="M0 2 H10 V8 H0 Z M0 2 L5 6 L10 2" stroke="#f5f5f5" stroke-width="0.8"/></svg>www.BrightNestMums.example</li>
        <li><svg viewBox="0 0 10 10"><circle cx="5" cy="5" r="5"/><path d="M0 5 H10 M5 0 V10" stroke="#f5f5f5" stroke-width="0.7"/></svg>lena@brightnestmums.example</li>
      </ul>
    </div>
  </section>
</body>
</html>
```